Updated website design needed for Radiology Group, Pine Hollow Imaging Partners

Clean, uncluttered, updated design needed for top regional Radiology Center. Focus on personal, patient oriented design, (not clinical). Should be simple and easy to navigate, with clear CTAs. Use blues, greens and photos of people in the Central Oregon outdoors.
Uncoded, PSD design only. 2 pages: Home page and one example interior page.
reference current site: http://www.phipclinic-example.com/
Sites they like:
http://www.valescanlabs-example.com/
http://www.tbmx-example.net/handler.cfm?event=practice,main
http://www.kestrelbonecare-example.com/

Medical Imaging

2 page

Sans Serif

• Personal and patient friendly.
• Lots of white space, clean and uncluttered. Clear CTAs, such as: Patient Bill Pay, Make an Appointment, Meet Our Doctors
• Use copy and contact information from the current site.
• Use outdoor images from Central Oregon, late Winter/ Spring (snow, light colors, spring green, for example)
• Include one example interior page, either Your Exam or Meet Our Doctors
• The client likes:
• Meet Our Doctors slider section, and big, easy to navigate Information Center on www.kestrelbonecare-example.com
• The personal feel of the Your Exam section on www.valescanlabs-example.com
• Blues and Greens, outdoorsy imagery
• The client does not like:
• complex drop down menus
• clinical feel
• Do not use lorum ipsum or dummy text.
• Do not use outdoor images from other regions. Do not use Summer (hot, poolside) or Fall (red/orange leaves) images.

```html
<!DOCTYPE html>
<html lang="en">
<head>
<meta charset="utf-8">
<title>Pine Hollow Imaging Partners</title>
<link rel="stylesheet" href="https://fonts.googleapis.com/css2?family=Ubuntu:wght@300;400;500;700&display=swap">
<style>
:root{
  --blue:#0a80c4;
  --blue-dark:#0669a3;
  --brand:#5a63a8;
  --green:#4a9a1e;
  --green-btn:#3f9a1a;
  --text:#555a60;
  --muted:#8a8f95;
  --dark:#3a3a3a;
  --darker:#2f2f2f;
  --light-bg:#eef0f4;
  --white:#ffffff;
}
*{margin:0;padding:0;box-sizing:border-box}
html,body{width:1200px;height:2740px;overflow:hidden}
body{font-family:"Ubuntu",sans-serif;color:var(--text);background:var(--white);position:relative}
section,header,footer,nav{position:absolute;left:0;width:1200px}
.abs{position:absolute}

/* header */
.site-header{top:0;height:95px;background:linear-gradient(#ffffff,#f1f2f6)}
.brand{left:131px;top:14px;display:flex;align-items:center;gap:12px}
.brand-mark{width:60px;height:62px;background:var(--brand)}
.brand-name{font-size:19px;font-weight:500;color:var(--brand);line-height:1.15;width:170px}
.top-links{right:131px;top:14px;font-size:13px;color:#333;display:flex;gap:14px}
.top-links span.sep{color:#333}
.call{right:131px;top:46px;font-size:22px;color:#333}
.call b{color:var(--green);font-weight:700}

/* nav */
.main-nav{top:95px;height:46px;background:var(--blue);display:flex;padding-left:131px}
.main-nav a{color:#fff;text-decoration:none;font-size:14px;line-height:46px;padding:0 21px}
.main-nav a.active{background:var(--blue-dark)}

/* hero */
.hero{top:141px;height:462px;background:linear-gradient(180deg,#7fb2d8 0%,#a9cbe2 35%,#5f8aa0 55%,#3d6a4a 80%,#2f5234 100%)}
.hero-caption{left:131px;top:255px;width:426px;height:116px;background:rgba(40,44,70,.72);padding:18px 26px}
.hero-caption h1{font-size:38px;font-weight:400;color:#fff}
.hero-caption p{font-size:20px;color:#fff;margin-top:4px}
.btn-green{background:var(--green-btn);color:#fff;font-size:14px;font-weight:500;display:inline-block;text-align:center;box-shadow:0 2px 0 #2d7410}
.hero .btn-green{left:155px;top:361px;width:207px;height:41px;line-height:41px;position:absolute}

/* welcome */
.welcome{top:603px;height:255px;text-align:center}
.section-title{font-size:26px;font-weight:400;color:#333}
.section-title em{font-style:normal;color:var(--brand)}
.welcome .section-title{margin-top:30px}
.welcome p{width:960px;margin:22px auto 0;font-size:13px;line-height:27px;color:var(--muted)}
.welcome .btn-green{width:120px;height:33px;line-height:33px;margin-top:20px;font-size:12px}

/* services */
.services{top:858px;height:430px;background:linear-gradient(160deg,#3f7c9c 0%,#2f6f92 50%,#2a5f80 100%);color:#fff}
.services .section-title{color:#fff;text-align:center;margin-top:36px}
.services .section-title b{font-weight:700}
.services .lead{text-align:center;font-size:13px;color:#bcd3e2;margin-top:10px}
.service{width:300px;display:flex;gap:14px}
.service svg{flex:none}
.service h3{font-size:17px;font-weight:500;color:#fff;margin-bottom:6px}
.service p{font-size:13px;line-height:25px;color:#c6d9e6}

/* doctors */
.doctors{top:1288px;height:429px;text-align:center}
.doctors .section-title{margin-top:34px}
.doctors .lead{font-size:13px;color:var(--muted);margin-top:10px}
.doctor{width:240px;text-align:center}
.doctor .photo{width:160px;height:160px;border-radius:50%;margin:0 auto;background:radial-gradient(circle at 50% 40%,#e7d4c6,#b8c6d4)}
.doctor h4{font-size:15px;font-weight:400;color:#333;margin-top:26px}
.doctor span{font-size:11px;color:var(--muted)}
.slider-arrow{top:224px}

/* appointment */
.appointment{top:1717px;height:380px;background:var(--light-bg)}
.appointment .photo{right:0;top:0;width:433px;height:380px;background:linear-gradient(90deg,#eef0f4 0%,#e3e8ee 30%,#d9dfe6 100%)}
.appointment h2{left:131px;top:36px;font-size:28px;font-weight:400;color:#333}
.appointment h2 b{color:var(--blue);font-weight:500}
.appointment .lead{left:131px;top:76px;font-size:13px;color:var(--muted)}
.field{font-size:12px;color:#666;border-bottom:2px solid #9ea4ab;padding-bottom:6px}
.field.focus{border-color:var(--blue)}
.btn-send{left:131px;top:290px;width:99px;height:33px;line-height:33px;background:var(--blue);color:#fff;text-align:center;font-size:14px;font-weight:500;box-shadow:0 2px 0 #05598a}

/* testimonial */
.testimonial{top:2097px;height:274px;text-align:center}
.testimonial .avatar{left:544px;top:-47px;width:112px;height:112px;border-radius:50%;border:4px solid #fff;background:radial-gradient(circle at 50% 40%,#e5cdb9,#9c7f6a)}
.testimonial blockquote{left:180px;top:98px;width:840px;font-size:14px;line-height:25px;color:#555}
.quote-mark{font-size:44px;color:#999;font-family:Georgia,serif}
.testimonial .name{left:0;width:1200px;top:190px;font-size:15px;font-weight:500;color:var(--green)}
.dots{left:537px;top:248px;display:flex;gap:4px}
.dots i{width:28px;height:3px;background:#ccc;display:block}
.dots i.on{background:var(--green)}

/* footer */
.site-footer{top:2371px;height:301px;background:var(--dark);color:#ddd}
.col{top:56px}
.col h5{font-size:18px;font-weight:400;color:#fff;margin-bottom:24px}
.quick-links li{list-style:none;font-size:13px;color:#ccc;line-height:28px}
.quick-links li::before{content:"•";color:var(--green);margin-right:10px}
.news p{font-size:12px;color:#ddd;line-height:20px;width:205px}
.news .input{width:205px;height:29px;background:#5a5a5a;font-size:11px;color:#bbb;line-height:29px;padding-left:10px;margin-top:22px}
.news .submit{width:95px;height:28px;background:var(--blue);color:#fff;font-size:14px;text-align:center;line-height:28px;margin-top:18px}
.hours .row{display:flex;gap:10px;margin-bottom:16px}
.hours .time{font-size:22px;color:#fff}
.hours .time small{font-size:22px}
.hours .time .to{color:#999}
.hours .sub{font-size:12px;color:#ccc}
.contact .row{display:flex;gap:14px;font-size:12px;color:#ddd;line-height:18px;margin-bottom:18px;align-items:flex-start}
.bottom-bar{top:2672px;height:68px;background:var(--darker)}
.bottom-bar .copy{left:131px;top:26px;font-size:12px;color:#ccc}
.social{left:934px;top:20px;display:flex;gap:8px}
.social i{width:26px;height:26px;border-radius:50%;border:2px solid var(--blue);display:block}
.social i:last-child{border-color:#d9503f}
</style>
</head>
<body>

<header class="site-header">
  <div class="brand abs"><div class="brand-mark"></div><div class="brand-name">Pine Hollow Imaging Partners</div></div>
  <div class="top-links abs"><span>Online Bill Pay</span><span class="sep">|</span><span>Appointments</span><span class="sep">|</span><span>Contact Us</span></div>
  <div class="call abs">Call Us : <b>(541) 555-0148</b></div>
</header>

<nav class="main-nav">
  <a class="active">Home</a><a>About Us</a><a>Our Services</a><a>For Patients</a><a>Our Physicians</a><a>For Physicians</a><a>PACS &amp; Documents</a><a>Our Locations</a>
</nav>

<section class="hero" role="img" aria-label="Photo of two hikers with backpacks on a rocky summit above a coastal valley">
  <div class="hero-caption abs">
    <h1>Smart technologies</h1>
    <p>Modern imaging Intelligence</p>
  </div>
  <span class="btn-green">Make an Appointment</span>
</section>

<section class="welcome">
  <h2 class="section-title">Welcome to <em>Pine Hollow Imaging Partners</em></h2>
  <p>Pine Hollow Imaging Partners is a diagnostic imaging corporation providing professional services to Central and Eastern Oregon hospitals and clinics as well as state-of-the-art services in its' own outpatient imaging center. PHIP was established by its' founder, Harold J. Whitcombe, MD when he opened his Central Oregon practice in 1947.</p>
  <span class="btn-green">Learn More »</span>
</section>

<section class="services">
  <h2 class="section-title">We Provide <b>Services</b></h2>
  <p class="lead">Our state-of-the-art outpatient imaging center provides professional services to Central Oregon Hospitals and Clinics.</p>

  <div class="service abs" style="left:131px;top:135px">
    <svg width="40" height="40" viewBox="0 0 40 40" fill="none" stroke="#fff" stroke-width="3"><path d="M20 4v32M10 12h20M8 20h24M10 28h20"/></svg>
    <div><h3>General Radiography</h3><p>We welcome patients for emergent<br>and walk-in plain films.[+]</p></div>
  </div>
  <div class="service abs" style="left:451px;top:135px">
    <svg width="40" height="40" viewBox="0 0 40 40"><circle cx="20" cy="20" r="17" fill="none" stroke="#fff" stroke-width="3"/><circle cx="20" cy="17" r="6" fill="#fff"/><text x="20" y="33" font-size="8" fill="#fff" text-anchor="middle" font-family="Ubuntu,sans-serif" font-weight="700">MRI</text></svg>
    <div><h3>Magnetic Resonance Imaging</h3><p>PHMRI has three convenient<br>locations Redmond, PHIP on the<br>eastside of Bend, and Riverbend Medical Center.[+]</p></div>
  </div>
  <div class="service abs" style="left:787px;top:135px">
    <svg width="40" height="40" viewBox="0 0 40 40" fill="none" stroke="#fff" stroke-width="4" stroke-linecap="round"><path d="M14 6c6 8 12 18 16 28M26 6c-6 8-12 18-16 28"/></svg>
    <div><h3>Digital Mammography</h3><p>Every 2 minutes there's a new breast<br>cancer diagnosis made.[+]</p></div>
  </div>
  <div class="service abs" style="left:131px;top:275px">
    <svg width="40" height="40" viewBox="0 0 40 40"><circle cx="20" cy="20" r="16" fill="none" stroke="#fff" stroke-width="4"/><circle cx="20" cy="20" r="6" fill="#fff"/><rect x="6" y="28" width="28" height="6" fill="#fff"/></svg>
    <div><h3>Computed Tomography</h3><p>PHIP now offers extended CT hours<br>at our eastside location.[+]</p></div>
  </div>
  <div class="service abs" style="left:451px;top:275px">
    <svg width="40" height="40" viewBox="0 0 40 40"><path d="M6 10h28l-4 24H10z" fill="#fff"/><circle cx="20" cy="22" r="6" fill="#2f6f92"/></svg>
    <div><h3>Ultrasound</h3><p>Advanced level obstetric, abdominal,<br>pelvic and small parts imaging.[+]</p></div>
  </div>
  <div class="service abs" style="left:787px;top:275px">
    <svg width="40" height="40" viewBox="0 0 40 40"><path d="M20 35L5 20a8 8 0 0 1 15-10a8 8 0 0 1 15 10z" fill="#fff"/><path d="M6 20h8l3-5 4 9 3-4h10" fill="none" stroke="#2f6f92" stroke-width="2.5"/></svg>
    <div><h3>Nuclear Medicine &amp; PET</h3><p>We provide PET scanning services<br>for Central and Eastern Oregon<br>communities. [+]</p></div>
  </div>
</section>

<section class="doctors">
  <h2 class="section-title">Meet <em>Our Doctors</em></h2>
  <p class="lead">It is a long established fact that a reader will be distracted by the readable content of a page when looking at its layout.</p>
  <svg class="abs slider-arrow" style="left:54px" width="24" height="56" viewBox="0 0 24 56"><path d="M22 2L2 28l20 26" fill="none" stroke="#bbb" stroke-width="2"/></svg>
  <svg class="abs slider-arrow" style="left:1122px" width="24" height="56" viewBox="0 0 24 56"><path d="M2 2l20 26L2 54" fill="none" stroke="#bbb" stroke-width="2"/></svg>
  <div class="doctor abs" style="left:92px;top:146px"><div class="photo" role="img" aria-label="Portrait photo of Dr. Mara Ellison"></div><h4>Dr. Mara Ellison (MD)</h4><span>Digital Mammography</span></div>
  <div class="doctor abs" style="left:351px;top:146px"><div class="photo" role="img" aria-label="Portrait photo of Dr. Owen Hartley"></div><h4>Dr. Owen Hartley (PhD)</h4><span>Digital Mammography</span></div>
  <div class="doctor abs" style="left:609px;top:146px"><div class="photo" role="img" aria-label="Portrait photo of Dr. Clara Voss"></div><h4>Dr. Clara Voss (MD)</h4><span>Digital Mammography</span></div>
  <div class="doctor abs" style="left:866px;top:146px"><div class="photo" role="img" aria-label="Portrait photo of Dr. Simon Radek"></div><h4>Dr. Simon Radek (PhD)</h4><span>Digital Mammography</span></div>
</section>

<section class="appointment">
  <div class="photo abs" role="img" aria-label="Photo of a smiling nurse with a stethoscope holding a tablet"></div>
  <h2 class="abs">Make an <b>Appointment</b></h2>
  <p class="lead abs">You can schedule an appointment by calling 541.555.0172</p>
  <div class="field focus abs" style="left:131px;top:128px;width:282px">Name</div>
  <div class="field abs" style="left:444px;top:128px;width:281px">Phone Number</div>
  <div class="field abs" style="left:131px;top:180px;width:282px">Email Address</div>
  <div class="field abs" style="left:444px;top:180px;width:281px">Appoinment Date</div>
  <div class="field abs" style="left:131px;top:233px;width:594px">Message</div>
  <div class="btn-send abs">SEND</div>
</section>

<section class="testimonial">
  <div class="avatar abs" role="img" aria-label="Portrait photo of Nora Pembridge"></div>
  <span class="quote-mark abs" style="left:152px;top:80px">&ldquo;</span>
  <blockquote class="abs">Lorem ipsum dolor sit amet, consectetuer adipiscing elit, sed diam nonummy nibh euismod tincidunt ut laoreet dolore magna aliquam erat volutpat. Nam vitae felis pretium, euismod ipsum nec, placerat turpis. Aenean eu gravida arcu, et consectetur orci Quisque posuere dolor in malesuada fermentum.</blockquote>
  <span class="quote-mark abs" style="left:1030px;top:134px">&rdquo;</span>
  <p class="name abs">Nora Pembridge</p>
  <div class="dots abs"><i class="on"></i><i></i><i></i></div>
</section>

<footer class="site-footer">
  <div class="col abs" style="left:131px">
    <h5>Quick Links</h5>
    <ul class="quick-links"><li>About Your Visit</li><li>Why Choose Us?</li><li>Patient Forms</li><li>Billing and Insurance</li><li>Locations and Maps</li><li>Appointments</li></ul>
  </div>
  <div class="col news abs" style="left:321px">
    <h5>Newsletter</h5>
    <p>Lorem Ipsum is simply dummy text of theand typesetting industry.</p>
    <div class="input">Email Address</div>
    <div class="submit">Submit</div>
  </div>
  <div class="col hours abs" style="left:577px">
    <h5>Opening Hours</h5>
    <div class="row">
      <svg width="24" height="24" viewBox="0 0 24 24" style="margin-top:4px"><circle cx="12" cy="12" r="10" fill="none" stroke="var(--green)" stroke-width="2.5"/><path d="M12 6v6l4 3" fill="none" stroke="var(--green)" stroke-width="2.5"/></svg>
      <div><div class="time">8:00<small>am</small> <span class="to">To</span> 9:00<small>pm</small></div><div class="sub">Monday to Saturday</div></div>
    </div>
    <div class="row">
      <svg width="24" height="24" viewBox="0 0 24 24" style="margin-top:4px"><circle cx="12" cy="12" r="10" fill="none" stroke="var(--green)" stroke-width="2.5"/><path d="M12 6v6l4 3" fill="none" stroke="var(--green)" stroke-width="2.5"/></svg>
      <div><div class="time">9:00<small>am</small> <span class="to">To</span> 6:00<small>pm</small></div><div class="sub">Sunday &amp; Public holiday</div></div>
    </div>
  </div>
  <div class="col contact abs" style="left:862px">
    <h5>Contact Us</h5>
    <div class="row"><svg width="14" height="20" viewBox="0 0 14 20"><path d="M7 0a7 7 0 0 1 7 7c0 5-7 13-7 13S0 12 0 7a7 7 0 0 1 7-7z" fill="var(--green)"/><circle cx="7" cy="7" r="2.5" fill="#3a3a3a"/></svg><span>Lorem Ipsum is simply dummy<br>Ridgefield, OR 97000</span></div>
    <div class="row"><svg width="14" height="16" viewBox="0 0 24 24"><path d="M6 2l4 5-2 3c1 3 3 5 6 6l3-2 5 4-3 4C10 22 2 14 2 5z" fill="var(--green)"/></svg><span>(541) 555-0148</span></div>
    <div class="row"><svg width="14" height="12" viewBox="0 0 14 12"><rect width="14" height="12" fill="var(--green)"/><path d="M0 1l7 5 7-5" fill="none" stroke="#3a3a3a" stroke-width="1.5"/></svg><span>info@phipclinic-example.com</span></div>
  </div>
</footer>

<div class="bottom-bar abs" style="left:0;width:1200px">
  <p class="copy abs">Copyright © 2016 Pine Hollow Imaging Partners I All Rights Reserved.</p>
  <div class="social abs"><i></i><i></i><i></i><i></i></div>
</div>

</body>
</html>
```